Hip / Cool Business Card for Custom Accessory Company

I would like to get a 2 sided design for standard size business cards, glossy (2 inches x 3.5 inches). Can be landscape or portrait layout! The design should include our logo (attached). The card should be extremely clear that the company is Tidy Pebble. Should also have our URL clear. Should also use the color scheme seen on our upcoming site, tidypebble.example. The font we use is called "hurry up." Other than that, please go-to-town. We are targeting 15-45 y.o. market, with a skew on the 20-30 crowd. We do custom and stock iPhone cases as well as Cufflinks, Winestoppers; see the website for more.
Updates

Project Deadline Extended
Reason: Extending in case the US July 4th Holiday is keeping people from working!!

Industry/Entity Type

Landscape

Requirements
Must have
• Must be clear that the website is tidypebble.example. Must be clear that custom designs are an option.
Nice to have
• images of our designs. examples of our designs.
Should not have
• hard on the eyes contrasting colors such as orange on black. green on blue. Should not have any fonts that are considered "old" like Times New Roman. But decorative fonts are fine.

```html
<!DOCTYPE html>
<html lang="en">
<head>
<meta charset="utf-8">
<title>Tidy Pebble Business Cards</title>
<link href="https://fonts.googleapis.com/css2?family=Lato:wght@400;700;900&display=swap" rel="stylesheet">
<style>
  :root {
    --teal: #2a9fa6;
    --teal-dark: #1f8a91;
    --ink: #1c1c1c;
    --muted: #3a3a3a;
    --card: #ffffff;
    --stage: #ecebe8;
    --ghost-a: #eef2f3;
    --ghost-b: #dfe6e8;
  }
  * { box-sizing: border-box; margin: 0; padding: 0; }
  html, body { width: 1200px; height: 913px; overflow: hidden; }
  body {
    background: var(--stage);
    font-family: "Lato", Arial, sans-serif;
    position: relative;
  }
  .card {
    position: absolute;
    width: 525px;
    height: 300px;
    background: var(--card);
    border-radius: 16px;
    overflow: hidden;
    box-shadow: 0 6px 18px rgba(0,0,0,0.12);
  }
  .card--front { left: 50px; top: 140px; }
  .card--back { left: 625px; top: 470px; }

  .ghost-mark {
    position: absolute;
    border-radius: 50%;
    background: radial-gradient(circle at 45% 45%, var(--ghost-a), var(--ghost-b));
    opacity: 0.8;
  }
  .card--front .ghost-mark { width: 300px; height: 300px; left: -90px; bottom: -120px; }
  .card--back .ghost-mark { width: 190px; height: 190px; right: 40px; top: -70px; opacity: 0.6; }

  .wordmark {
    position: absolute;
    display: flex;
    align-items: center;
    gap: 10px;
    font-weight: 900;
    color: var(--ink);
    text-transform: uppercase;
    letter-spacing: 1px;
    white-space: nowrap;
  }
  .wordmark__dot {
    width: 34px; height: 34px; border-radius: 50%;
    background: var(--teal);
    flex: none;
  }
  .card--front .wordmark { left: 230px; top: 120px; font-size: 30px; }
  .card--back .wordmark { left: 40px; top: 95px; font-size: 30px; }

  .front-info {
    position: absolute;
    right: 48px; top: 218px;
    text-align: right;
  }
  .site-url {
    color: var(--teal);
    font-weight: 700;
    font-size: 15px;
  }
  .offer {
    margin-top: 4px;
    color: var(--muted);
    font-size: 12px;
    letter-spacing: 0.5px;
  }

  .edge-tab {
    position: absolute; right: 0; top: 38px;
    width: 14px; height: 40px;
    background: var(--teal);
    border-radius: 4px 0 0 4px;
  }
  .base-band {
    position: absolute; left: 0; right: 0; bottom: 0;
    height: 14px;
    background: linear-gradient(90deg, var(--teal), var(--teal-dark));
  }

  .person {
    position: absolute; right: 30px; top: 52px;
    text-align: right;
  }
  .person__name { color: var(--teal); font-weight: 700; font-size: 15px; }
  .person__role { color: var(--muted); font-size: 11px; margin-top: 2px; }

  .contacts {
    position: absolute; right: 22px; top: 118px;
    list-style: none;
    text-align: right;
    color: var(--teal);
    font-size: 11.5px;
    line-height: 17px;
  }
  .contacts li { display: flex; justify-content: flex-end; align-items: center; gap: 6px; }
  .contacts svg { width: 10px; height: 10px; fill: var(--ink); }

  .address {
    position: absolute; left: 40px; bottom: 48px;
    font-style: normal;
    color: var(--teal);
    font-size: 13px;
    line-height: 17px;
  }
</style>
</head>
<body>

  <section class="card card--front">
    <div class="ghost-mark" role="img" aria-label="Faint oversized mascot decoration"></div>
    <div class="wordmark"><span class="wordmark__dot"></span>Tidy Pebble</div>
    <div class="front-info">
      <div class="site-url">www.tidypebble.example</div>
      <div class="offer">Custom designs made to order</div>
    </div>
  </section>

  <section class="card card--back">
    <div class="ghost-mark" role="img" aria-label="Faint mascot decoration"></div>
    <div class="edge-tab"></div>
    <div class="wordmark"><span class="wordmark__dot"></span>Tidy Pebble</div>

    <div class="person">
      <div class="person__name">Rowan Ellery</div>
      <div class="person__role">Founder &amp; CEO</div>
    </div>

    <ul class="contacts">
      <li>555.010.0100
        <svg viewBox="0 0 10 10"><path d="M2 1 L4 1 L4.5 3 L3.4 3.8 C4 5.2 4.8 6 6.2 6.6 L7 5.5 L9 6 L9 8 C5 8.5 1.5 5 2 1 Z"/></svg></li>
      <li>555.010.0199
        <svg viewBox="0 0 10 10"><rect x="3" y="0.5" width="4" height="9" rx="0.8"/></svg></li>
      <li>hello@tidypebble.example
        <svg viewBox="0 0 10 10"><path d="M0.5 2 H9.5 V8 H0.5 Z M0.5 2 L5 5.5 L9.5 2" stroke="#fff" stroke-width="0.7"/></svg></li>
      <li>www.tidypebble.example
        <svg viewBox="0 0 10 10"><circle cx="5" cy="5" r="4.5"/><path d="M0.5 5 H9.5 M5 0.5 V9.5" stroke="#fff" stroke-width="0.7"/></svg></li>
    </ul>

    <address class="address">
      <div>Tidy Pebble</div>
      <div>418 Quarry Lane Suite 12</div>
      <div>Brookvale, VA 20000</div>
    </address>

    <div class="base-band"></div>
  </section>

</body>
</html>
```